Business Card Design (NEW FILES)

ATTENTION: New vector files are available. Please update your design to reflect/use the new (better resolution) logo images.

Seeking a unique and professional business card design for a commercial drone photography/videography business. The layout should feature
the logo (attached) and include the following information:
Owen Tarrick
614-502-7738
www.skylarkreelworks.example
NRD Certified Remote Pilot

Owen Tarrick

```html
<!DOCTYPE html>
<html lang="en">
<head>
<meta charset="utf-8">
<title>Skylark Reelworks – Business Card</title>
<link href="https://fonts.googleapis.com/css2?family=Open+Sans:wght@400;600;700&display=swap" rel="stylesheet">
<style>
  :root {
    --backdrop: #222222;
    --navy: #141a4b;
    --navy-deep: #10153f;
    --navy-raised: #263a8a;
    --orange: #ef8a48;
    --white: #ffffff;
    --faint: rgba(120, 130, 190, 0.22);
  }
  * { box-sizing: border-box; margin: 0; padding: 0; }
  html, body { width: 1200px; height: 780px; overflow: hidden; background: var(--backdrop); }
  body { font-family: "Open Sans", Arial, sans-serif; color: var(--white); }
  .canvas {
    position: relative; width: 1200px; height: 780px;
    display: flex; align-items: center; justify-content: center; gap: 48px;
  }
  .card {
    position: relative; width: 540px; height: 309px;
    background: var(--navy); overflow: hidden;
    box-shadow: 0 18px 40px rgba(0,0,0,0.55);
  }
  /* Front */
  .brand {
    position: absolute; left: 34px; top: 34px;
    display: flex; align-items: center; gap: 10px;
  }
  .brand-name {
    font-size: 26px; font-weight: 600; color: var(--white);
    letter-spacing: 0.5px; line-height: 1;
  }
  .brand-dot { width: 16px; height: 16px; border-radius: 50%; background: var(--orange); }
  .contact { position: absolute; left: 34px; top: 150px; list-style: none; }
  .contact li {
    display: flex; align-items: center; gap: 9px;
    font-size: 13px; line-height: 1; margin-bottom: 10px;
  }
  .contact svg { width: 13px; height: 13px; flex: none; }
  .person { position: absolute; right: 34px; top: 112px; text-align: right; }
  .person-name { font-size: 27px; font-weight: 700; line-height: 1.1; }
  .person-name .first { color: var(--orange); }
  .person-role { font-size: 14px; margin-top: 2px; }
  .edge-bar {
    position: absolute; right: 0; top: 118px;
    width: 14px; height: 48px; background: var(--orange);
  }
  .credentials {
    position: absolute; right: 34px; bottom: 30px;
    text-align: right; font-size: 14px; line-height: 1.4; z-index: 1;
  }
  .faint-mark {
    position: absolute; right: 120px; bottom: -30px;
    width: 150px; height: 150px; border-radius: 50%; background: var(--faint);
  }
  /* Back */
  .card-back { display: flex; align-items: center; justify-content: center; background: var(--navy-deep); }
  .back-brand { display: flex; align-items: center; gap: 14px; }
  .back-brand .brand-name { font-size: 36px; color: var(--navy-raised); }
  .back-brand .brand-dot { width: 22px; height: 22px; background: var(--navy-raised); }
</style>
</head>
<body>
<main class="canvas">
  <section class="card card-front" aria-label="Business card front">
    <div class="brand">
      <span class="brand-name">Skylark Reelworks</span>
      <span class="brand-dot"></span>
    </div>

    <ul class="contact">
      <li>
        <svg viewBox="0 0 16 16" aria-hidden="true"><path fill="var(--orange)" d="M3.5 1.5l2.5 0 1 3.5-1.8 1.2a8 8 0 0 0 4.6 4.6L11 9l3.5 1v2.5c0 1-1 2-2 2A11 11 0 0 1 1.5 3.5c0-1 1-2 2-2z"/></svg>
        <span>614-502-7738</span>
      </li>
      <li>
        <svg viewBox="0 0 16 16" aria-hidden="true"><circle cx="8" cy="8" r="6.5" fill="none" stroke="var(--orange)" stroke-width="1.6"/><path d="M1.5 8h13M8 1.5c-3 3.5-3 9.5 0 13M8 1.5c3 3.5 3 9.5 0 13" fill="none" stroke="var(--orange)" stroke-width="1.3"/></svg>
        <span>www.skylarkreelworks.example</span>
      </li>
      <li>
        <svg viewBox="0 0 16 16" aria-hidden="true"><rect x="1.5" y="3.5" width="13" height="9" fill="none" stroke="var(--orange)" stroke-width="1.6"/><path d="M1.5 3.5L8 9l6.5-5.5" fill="none" stroke="var(--orange)" stroke-width="1.4"/></svg>
        <span>info@skylarkreelworks.example</span>
      </li>
    </ul>

    <div class="person">
      <p class="person-name"><span class="first">Owen</span> Tarrick</p>
      <p class="person-role">Owner</p>
    </div>
    <div class="edge-bar"></div>

    <div class="faint-mark"></div>
    <div class="credentials">
      <p>NRD Certified Remote Pilot</p>
      <p>Fully Insured</p>
    </div>
  </section>

  <section class="card card-back" aria-label="Business card back">
    <div class="back-brand">
      <span class="brand-name">Skylark Reelworks</span>
      <span class="brand-dot"></span>
    </div>
  </section>
</main>
</body>
</html>
```